Business card por a urban DJ, up scale audience target

Need a sober design, modern, conservative colors but i can consider some options, y play rnb, hip hop, EDM and top40.

Business card for contact and personal info, double sided, use logo attrached please; im 42 so i need a card acording to my age an target audience.

Target Market(s)

Adult people, up scale audience

Industry/Entity Type

Music Download

Contact Information for Business Card

Cel (318) 4207265518 www.lumadrift.com

Requirements
Must have
• open mind
Nice to have
• open mind
Should not have
• DJ

```html
<!DOCTYPE html>
<html lang="en">
<head>
<meta charset="utf-8">
<title>Lumadrift Business Card</title>
<link href="https://fonts.googleapis.com/css2?family=Source+Sans+3:wght@400;700&display=swap" rel="stylesheet">
<style>
  :root {
    --backdrop: #8a8a8a;
    --card-light: #ffffff;
    --card-dark: #2a2928;
    --ink: #2a2928;
    --ink-soft: #333333;
    --mark-faint: #3a3937;
  }
  html, body {
    margin: 0;
    padding: 0;
    width: 1200px;
    height: 900px;
    overflow: hidden;
    background: var(--backdrop);
    font-family: "Source Sans 3", "Myriad Pro", Arial, sans-serif;
  }
  .canvas {
    position: relative;
    width: 1200px;
    height: 900px;
  }
  .card {
    position: absolute;
    top: 170px;
    width: 347px;
    height: 561px;
    overflow: hidden;
  }
  .card--front { left: 259px; background: var(--card-light); }
  .card--back  { left: 631px; background: var(--card-dark); }

  .card__tab {
    position: absolute;
    left: 102px;
    width: 143px;
    height: 30px;
    background: var(--ink);
  }
  .card__tab--top { top: 0; }
  .card__tab--bottom { bottom: 0; height: 28px; }

  .brand {
    position: absolute;
    left: 0;
    width: 100%;
    text-align: center;
  }
  .brand__name {
    display: block;
    font-weight: 700;
    font-size: 50px;
    letter-spacing: 1px;
    line-height: 1;
  }
  .card--front .brand { top: 128px; }
  .card--front .brand__name { color: var(--ink); }
  .card--back .brand { top: 253px; }
  .card--back .brand__name { color: var(--mark-faint); font-size: 54px; }

  .person {
    position: absolute;
    top: 276px;
    left: 0;
    width: 100%;
    text-align: center;
    color: var(--ink);
  }
  .person__name {
    margin: 0;
    font-weight: 400;
    font-size: 26px;
    line-height: 1.1;
    letter-spacing: 0.2px;
  }
  .person__role {
    margin: 4px 0 0;
    font-size: 15px;
    color: var(--ink-soft);
  }

  .contact {
    position: absolute;
    top: 348px;
    left: 0;
    width: 100%;
    margin: 0;
    padding: 0;
    list-style: none;
    text-align: center;
    font-size: 15px;
    color: var(--ink-soft);
  }
  .contact__item {
    height: 22px;
    line-height: 22px;
  }
  .contact__icon {
    width: 11px;
    height: 11px;
    margin-right: 8px;
    vertical-align: -1px;
    fill: var(--ink);
  }

  .address {
    position: absolute;
    top: 465px;
    left: 0;
    width: 100%;
    text-align: center;
    font-style: normal;
    font-size: 15px;
    line-height: 17px;
    color: var(--ink-soft);
  }
</style>
</head>
<body>
<main class="canvas">
  <section class="card card--front" aria-label="Card front">
    <div class="card__tab card__tab--top"></div>

    <div class="brand">
      <span class="brand__name">LUMADRIFT</span>
    </div>

    <div class="person">
      <h1 class="person__name">DANIEL REYES</h1>
      <p class="person__role">Managing Director</p>
    </div>

    <ul class="contact">
      <li class="contact__item">
        <svg class="contact__icon" viewBox="0 0 12 12" aria-hidden="true">
          <path d="M1 3.5 C1 2 3 1 6 1 S11 2 11 3.5 V4.5 H8.5 V3.3 C7.5 3 4.5 3 3.5 3.3 V4.5 H1 Z M3 5.5 H9 L10.5 10.5 H1.5 Z"/>
        </svg>(318) 4207265518
      </li>
      <li class="contact__item">
        <svg class="contact__icon" viewBox="0 0 12 12" aria-hidden="true">
          <path d="M1 2.5 H11 V9.5 H1 Z M1.6 3 L6 6.4 L10.4 3 Z" fill-rule="evenodd"/>
        </svg>info@lumadrift.com
      </li>
    </ul>

    <address class="address">
      1234, Address Goes Here<br>
      Country Name, 123456
    </address>

    <div class="card__tab card__tab--bottom"></div>
  </section>

  <section class="card card--back" aria-label="Card back">
    <div class="brand">
      <span class="brand__name">LUMADRIFT</span>
    </div>
  </section>
</main>
</body>
</html>
```